Vernac Law Business cards and stationary design project

We are looking for a stationary design for business cards (double sided), 8x10, 5x7, and legal and standard envelopes.

We would like the design to match the logo that we have already.
Color palate preferred is Teal, White, grey and any others that will look good for a professional law firm.

We would like this statement: "RELATIONSHIPS. RESPECT. RESULT" to be on the back of the business cards and maybe on the stationary if it looks good.

Please see link to website for more information: www.vernac-law.example

Target Market(s)

Potential clients that need Attorney services.

Industry/Entity Type

Law Firm

Contact Information for Business Card

We would like the front and back to be two different colors. Current business cards are teal front, grey back and are a vertical design. We are open to options with colors.

Font styles to use
Serif

Colors
33a6d7
33b8a4
b9b9b9
5c5c5c

Requirements
Must have
• Logo supplied needs to go on the card and stationary.
• Match website color palate, www.vernac-law.example
• Be professional and not too wordy.
• Criminal Law, Civil Litigation, Personal Injury, Restraining Orders need to be on the card.
Nice to have
• RELATIONSHIPS. RESPECT. RESULTS. on the back of the card.
Should not have
• Not be too busy/wordy or too flashy.

```html
<!DOCTYPE html>
<html lang="en">
<head>
<meta charset="utf-8">
<title>Vernac Law – Business Card</title>
<link rel="stylesheet" href="https://fonts.googleapis.com/css2?family=Cinzel:wght@400;500&family=Crimson+Text:wght@400&display=swap">
<style>
  :root {
    --teal: #12899a;
    --white: #ffffff;
    --ink-grey: #4f4f4f;
    --backdrop: #505050;
    --display: "Cinzel", serif;
    --body: "Crimson Text", serif;
  }
  * { box-sizing: border-box; margin: 0; padding: 0; }
  html, body {
    width: 1105px;
    height: 1200px;
    overflow: hidden;
    background: var(--backdrop);
  }
  .sheet { position: relative; width: 1105px; height: 1200px; }

  .card {
    position: absolute;
    left: 196px;
    width: 719px;
    height: 410px;
  }
  .card--front { top: 146px; background: var(--teal); }
  .card--back  { top: 602px; background: var(--white); }

  .firm-name {
    position: absolute;
    left: 0;
    width: 357px;
    top: 178px;
    text-align: center;
    font-family: var(--display);
    font-weight: 400;
    font-size: 34px;
    letter-spacing: 1px;
    color: var(--white);
  }

  .contact-panel {
    position: absolute;
    left: 357px;
    top: 90px;
    width: 362px;
    height: 231px;
    background: var(--white);
    padding: 26px 0 0 36px;
  }
  .person-name {
    font-family: var(--display);
    font-weight: 500;
    font-size: 31px;
    line-height: 1;
    color: var(--teal);
    letter-spacing: 0.5px;
  }
  .person-title {
    margin-top: 6px;
    font-family: var(--display);
    font-size: 21px;
    color: var(--ink-grey);
    letter-spacing: 0.5px;
  }
  .contact-list { list-style: none; margin-top: 24px; }
  .contact-list li {
    display: flex;
    align-items: center;
    gap: 14px;
    font-family: var(--body);
    font-size: 21px;
    line-height: 31px;
    color: var(--ink-grey);
  }
  .contact-list svg { width: 17px; height: 17px; flex: none; fill: var(--teal); }

  .back-name {
    position: absolute;
    left: 0; right: 0;
    top: 140px;
    text-align: center;
    font-family: var(--display);
    font-size: 62px;
    color: var(--teal);
    letter-spacing: 1px;
  }
  .tagline {
    position: absolute;
    left: 0; right: 0;
    top: 322px;
    text-align: center;
    font-family: var(--display);
    font-size: 23px;
    letter-spacing: 1.5px;
    color: var(--teal);
  }
  .practice-areas {
    position: absolute;
    left: 0; right: 0;
    top: 352px;
    text-align: center;
    font-family: var(--body);
    font-size: 22px;
    color: var(--ink-grey);
  }
</style>
</head>
<body>
<main class="sheet">
  <section class="card card--front" aria-label="Business card front">
    <div class="firm-name">Vernac Law</div>
    <div class="contact-panel">
      <div class="person-name">Maren Ostler</div>
      <div class="person-title">Trial Lawyer</div>
      <ul class="contact-list">
        <li>
          <svg viewBox="0 0 24 24" aria-hidden="true"><path d="M6.6 10.8a15.1 15.1 0 0 0 6.6 6.6l2.2-2.2c.3-.3.7-.4 1-.2 1.1.4 2.3.6 3.6.6.6 0 1 .4 1 1V20c0 .6-.4 1-1 1A17 17 0 0 1 3 4c0-.6.4-1 1-1h3.5c.6 0 1 .4 1 1 0 1.3.2 2.5.6 3.6.1.3 0 .7-.2 1z"/></svg>
          (555) 014-2387
        </li>
        <li>
          <svg viewBox="0 0 24 24" aria-hidden="true"><path d="M2 5h20v14H2z M3.5 6.5 12 12.5l8.5-6H3.5z" fill-rule="evenodd"/></svg>
          maren@vernac-law.example
        </li>
        <li>
          <svg viewBox="0 0 24 24" aria-hidden="true"><path d="M12 2a10 10 0 1 0 0 20 10 10 0 0 0 0-20zm-1 17.9A8 8 0 0 1 4.1 11L9 16v1a2 2 0 0 0 2 2zm6.9-2.5A2 2 0 0 0 16 16h-1v-3a1 1 0 0 0-1-1H8v-2h2a1 1 0 0 0 1-1V7h2a2 2 0 0 0 2-2v-.4a8 8 0 0 1 2.9 12.8z"/></svg>
          www.vernac-law.example
        </li>
      </ul>
    </div>
  </section>

  <section class="card card--back" aria-label="Business card back">
    <div class="back-name">Vernac Law</div>
    <p class="tagline">RELATIONSHIPS. RESPECT. RESULTS.</p>
    <p class="practice-areas">Criminal Law, Civil Litigation/Personal Injury , Restraining</p>
  </section>
</main>
</body>
</html>
```